Advertising company unique advertising platform

we need a logo design for a new company based in Australia Melbourne. We develop innovated advertising platform where consumer can use this platform to get regular discount, as business owner they can use this platform for free advertisement. Payment for this advertisement platform only payable every two weeks, when I generate revenue for their business

Industry/Entity Type

Advertising

Contact Information for Business Card

Dale Morven | Co-Founder |Managing Director
Suite 718 240 Wattlebrook Lane Melbourne Vic 3000

ABN 38 614 207 923
Tel: +61 0487 259 318 | Email: dale.morven@plivorantu.com

Font styles to use
Decorative
Script

Requirements
Must have
• Try few different design and some round corner business card
Should not have
• One round corner business card...try 4 different colour background not only black, make sure two side is designed. Be creative so imagine you are giving this to a client make sure has wow factor, if you can also try one design with engrave like all the logo, words look 3d feel
• The word Advertising Platform use attached file font

```html
<!DOCTYPE html>
<html lang="en">
<head>
<meta charset="utf-8">
<title>Kestrel Loop — Business Card</title>
<link rel="stylesheet" href="https://fonts.googleapis.com/css2?family=Roboto:wght@400;500;700&display=swap">
<style>
  :root{
    --page:#ecebe8;
    --card-dark:#242424;
    --card-back:#2a211c;
    --accent-red:#e5472c;
    --accent-teal:#35d6b2;
    --glow:#f4d64a;
    --text-light:#f2f2f2;
  }
  *{box-sizing:border-box;margin:0;padding:0}
  html,body{width:1200px;height:886px;overflow:hidden;background:var(--page)}
  body{position:relative;font-family:"Roboto",Arial,sans-serif}

  .card{position:absolute;width:560px;height:320px;border-radius:20px;overflow:hidden;
        box-shadow:0 10px 28px rgba(0,0,0,.25)}

  /* back side */
  .card--back{left:70px;top:80px;background:var(--card-back)}
  .card--back .pattern-fill{position:absolute;inset:0;width:100%;height:100%}
  .brand{position:absolute;left:0;right:0;top:112px;display:flex;align-items:center;justify-content:center;gap:16px}
  .brand__dot{width:34px;height:34px;border-radius:50%;background:var(--accent-red)}
  .brand__name{font-weight:700;font-size:44px;color:var(--accent-red);letter-spacing:1px}
  .website{position:absolute;left:0;right:0;top:236px;text-align:center;color:var(--text-light);
           font-size:14px;letter-spacing:6px}

  /* front side */
  .card--front{left:570px;top:486px;background:var(--card-dark)}
  .details{position:absolute;left:40px;top:40px;color:var(--text-light)}
  .details__name{font-size:24px;font-weight:700;color:var(--accent-red);text-transform:uppercase;letter-spacing:.5px}
  .details__role{font-size:15px;font-weight:700;color:var(--accent-teal);text-transform:uppercase;line-height:1.25;margin-top:4px}
  .details__info{font-size:14px;line-height:1.4;margin-top:12px}
  .details__contact{font-size:14px;line-height:1.5;margin-top:8px;list-style:none}
  .details__contact li{display:flex;align-items:center;gap:8px}
  .details__contact svg{width:12px;height:12px;fill:var(--accent-red);flex:none}
  .base-stripe{position:absolute;left:0;bottom:0;width:100%;height:14px;background:var(--accent-red)}
  .feature-block{position:absolute;right:50px;top:56px;width:150px;height:264px}
</style>
</head>
<body>

<section class="card card--back" aria-label="Card back">
  <svg class="pattern-fill" role="img" aria-label="Dark repeating brand pattern in brown and teal tones" viewBox="0 0 560 320" preserveAspectRatio="none">
    <defs>
      <radialGradient id="backTone" cx="50%" cy="50%" r="70%">
        <stop offset="0" stop-color="#3a2c24"/>
        <stop offset="1" stop-color="#1f1915"/>
      </radialGradient>
    </defs>
    <rect width="560" height="320" fill="url(#backTone)"/>
  </svg>
  <div class="brand">
    <span class="brand__dot"></span>
    <span class="brand__name">Kestrel Loop</span>
  </div>
  <p class="website">www.plivorantu.com</p>
</section>

<section class="card card--front" aria-label="Card front">
  <div class="details">
    <h1 class="details__name">Dale Morven</h1>
    <p class="details__role">Co-Founder<br>Managing Director</p>
    <p class="details__info">Plivo Rantu<br>ABN 38 614 207 923<br>Suite 718 240 Wattlebrook Lane<br>Melbourne Vic 3000</p>
    <ul class="details__contact">
      <li><svg viewBox="0 0 24 24" aria-hidden="true"><path d="M6.6 10.8a15 15 0 0 0 6.6 6.6l2.2-2.2a1 1 0 0 1 1-.25 11.4 11.4 0 0 0 3.6.57 1 1 0 0 1 1 1V20a1 1 0 0 1-1 1A17 17 0 0 1 3 4a1 1 0 0 1 1-1h3.5a1 1 0 0 1 1 1c0 1.25.2 2.45.57 3.57a1 1 0 0 1-.25 1z"/></svg>+61 0487 259 318</li>
      <li><svg viewBox="0 0 24 24" aria-hidden="true"><path d="M2 5h20v14H2z M2 5l10 8 10-8" /></svg>dale.morven@plivorantu.com</li>
    </ul>
  </div>
  <div class="base-stripe"></div>
  <svg class="feature-block" role="img" aria-label="Large orange accent block with warm glow" viewBox="0 0 150 264" preserveAspectRatio="none">
    <defs>
      <radialGradient id="warmGlow" cx="55%" cy="45%" r="45%">
        <stop offset="0" stop-color="#f4d64a"/>
        <stop offset="0.5" stop-color="#f08a35"/>
        <stop offset="1" stop-color="#e5472c"/>
      </radialGradient>
    </defs>
    <rect width="150" height="264" fill="url(#warmGlow)"/>
  </svg>
</section>

</body>
</html>
```